Manifesto

I want a manifesto with the following five manifestos for our Not for Profit

- We are a For-purpose organisation
- Every service we offer is free
- Every product we sell funds our services
- Every financial transaction is transparent
- Our service is for the greater good
- Our purpose is always to serve the people
- We are a for purpose organisation

Its to go with this website logo/look/feel www.brightharbour.co.nz

Two attachments:

1. I quite like this look/feel of a manifesto (see attached), I want something clean, professional but I also quite like either Retro modern look feel also like a fresh, and uplifting as its for sick people coming to see us and our funds where anyone buys a product are used for helping those who are sick with healing......so needs something conveyed that is fresh, uplifing yet professional.
2. This attachment is how I wrote this down when inspired of how I wanted Bright Harbour to operate. This is our values chart. It has to say

Also check out our website for our logo, look etc.. it doesnt have to be the same but red somewhere would link back to logo. www.brightharbour.co.nz .

Industry/Entity Type

Financial

```html
<!DOCTYPE html>
<html lang="en">
<head>
<meta charset="utf-8">
<title>Bright Harbour Manifesto</title>
<link href="https://fonts.googleapis.com/css2?family=Alfa+Slab+One&family=Arvo:wght@700&family=Lobster&family=Lobster+Two:ital,wght@1,700&display=swap" rel="stylesheet">
<style>
  :root {
    --page: #ffffff;
    --paper-light: #ececec;
    --paper-mid: #dcdcdc;
    --paper-edge: #c9c9c9;
    --ink: #3b3b3b;
    --red: #c4122a;
    --rule: #3b3b3b;
  }
  html, body {
    margin: 0;
    padding: 0;
    width: 1200px;
    height: 1000px;
    overflow: hidden;
    background: var(--page);
  }
  .canvas {
    display: block;
    width: 1200px;
    height: 1000px;
  }
  .slab-heavy { font-family: "Alfa Slab One", "Rockwell", serif; }
  .slab { font-family: "Arvo", "Rockwell", serif; font-weight: 700; }
  .script { font-family: "Lobster", "Brush Script MT", cursive; }
  .script-small { font-family: "Lobster Two", "Lobster", cursive; font-style: italic; font-weight: 700; }
  .ink { fill: var(--ink); }
  .red { fill: var(--red); }
  .lift { filter: url(#lift); }
  .rule { fill: var(--rule); }
  .web { font-family: "Arvo", serif; font-weight: 400; fill: var(--ink); letter-spacing: 2px; }
</style>
</head>
<body>
<svg class="canvas" viewBox="0 0 1200 1000" xmlns="http://www.w3.org/2000/svg" role="img" aria-label="Bright Harbour values manifesto poster">
  <defs>
    <radialGradient id="paper" cx="50%" cy="45%" r="75%">
      <stop offset="0%" stop-color="var(--paper-light)"/>
      <stop offset="70%" stop-color="var(--paper-mid)"/>
      <stop offset="100%" stop-color="var(--paper-edge)"/>
    </radialGradient>
    <filter id="lift" x="-5%" y="-10%" width="110%" height="130%">
      <feDropShadow dx="1.5" dy="2" stdDeviation="0.6" flood-color="#ffffff" flood-opacity="0.9"/>
    </filter>
  </defs>

  <rect class="poster" x="289" y="52" width="631" height="892" fill="url(#paper)"/>

  <g class="manifesto lift">
    <!-- Section 1 -->
    <text class="slab-heavy ink" x="314" y="122" font-size="56" textLength="306" lengthAdjust="spacingAndGlyphs">WE ARE A</text>
    <text class="slab-heavy red" x="314" y="170" font-size="44" textLength="306" lengthAdjust="spacingAndGlyphs">FOR PURPOSE</text>
    <text class="slab-heavy red" x="314" y="212" font-size="40" textLength="308" lengthAdjust="spacingAndGlyphs">ORGANISATION</text>

    <text class="script red" x="660" y="112" font-size="38" textLength="236" lengthAdjust="spacingAndGlyphs">Every Service</text>
    <text class="slab ink" x="664" y="144" font-size="26" textLength="232" lengthAdjust="spacing">we offer is</text>
    <text class="slab ink" x="664" y="208" font-size="74" textLength="232" lengthAdjust="spacing">FREE</text>

    <path class="rule" d="M313,232 C450,228 760,236 897,230 C760,239 450,235 313,232Z"/>

    <!-- Section 2 -->
    <text class="slab-heavy red" x="313" y="300" font-size="62" textLength="584" lengthAdjust="spacingAndGlyphs">EVERY PRODUCT</text>
    <text class="slab ink" x="313" y="343" font-size="36" textLength="584" lengthAdjust="spacingAndGlyphs">we sell funds our services</text>

    <path class="rule" d="M313,366 C450,362 760,370 897,364 C760,373 450,369 313,366Z"/>

    <!-- Section 3 -->
    <text class="slab-heavy red" x="313" y="440" font-size="58" textLength="266" lengthAdjust="spacing">EVERY</text>
    <text class="slab-heavy red" x="313" y="476" font-size="30" textLength="266" lengthAdjust="spacing">FINANCIAL</text>
    <text class="slab ink" x="313" y="510" font-size="27" textLength="266" lengthAdjust="spacing">TRANSACTION</text>
    <text class="slab ink" x="313" y="537" font-size="26" textLength="266" lengthAdjust="spacing">is transparent</text>

    <text class="slab ink" x="625" y="418" font-size="27" textLength="270" lengthAdjust="spacing">OUR SERVICE IS</text>
    <text class="script red" x="627" y="463" font-size="46" textLength="268" lengthAdjust="spacingAndGlyphs">for the greater</text>
    <text class="slab-heavy red" x="618" y="537" font-size="82" textLength="276" lengthAdjust="spacingAndGlyphs">GOOD</text>

    <path class="rule" d="M313,566 C450,562 760,570 897,564 C760,573 450,569 313,566Z"/>

    <!-- Section 4 -->
    <text class="slab ink" x="313" y="640" font-size="56" textLength="584" lengthAdjust="spacing">OUR PURPOSE IS</text>
    <text class="script red" x="314" y="688" font-size="50" textLength="582" lengthAdjust="spacingAndGlyphs">always to serve the people</text>

    <path class="rule" d="M313,725 C450,721 760,729 897,723 C760,732 450,728 313,725Z"/>

    <!-- Section 5 -->
    <text class="slab ink" x="313" y="782" font-size="46" textLength="587" lengthAdjust="spacingAndGlyphs">WE ARE A FOR PURPOSE</text>
    <text class="script red" x="313" y="870" font-size="106" textLength="582" lengthAdjust="spacingAndGlyphs">organisation</text>
  </g>

  <g class="signature">
    <text class="script-small ink" x="619" y="905" font-size="18" text-anchor="middle">Bright Harbour Manifesto</text>
    <text class="web" x="604" y="928" font-size="14" text-anchor="middle">www.brightharbour.co.nz</text>
  </g>
</svg>
</body>
</html>
```